Business Cards, Letterhead, Envelopes etc.
Need design that fits with tech saavy customers
Business Cards, Letterhead, Envelopes etc.  -
Creative Brief
Use specific fonts
Use same font or one that works with the logo
Cutting-Edge
Dean R. Marlow
President
418 Bellwick Street Palo Alto, CA 94306
dean@quevrafin.com
quevrafin.com
CA DRE: #00471362, NMLS: #517294
Need design for business cards, letterhead, #10 envelopes and mailing labels for package shipments.

```html
<!DOCTYPE html>
<html lang="en">
<head>
<meta charset="utf-8">
<title>Quevrafin Stationery Set</title>
<link href="https://fonts.googleapis.com/css2?family=Nunito:wght@400;700;800&family=Tinos:wght@400;700&display=swap" rel="stylesheet">
<style>
  :root {
    --stage-outer: #8e8e8e;
    --stage-inner: #a7a7a7;
    --paper: #ffffff;
    --brand-blue: #1d4fa3;
    --brand-deep: #0b2c6a;
    --brand-light: #4f86d6;
    --ink: #2b2b2b;
    --ink-soft: #6b6b6b;
  }
  * { box-sizing: border-box; margin: 0; padding: 0; }
  html, body { width: 1200px; height: 626px; overflow: hidden; }
  body {
    background: var(--stage-outer);
    font-family: "Tinos", "Times New Roman", serif;
    color: var(--ink);
    position: relative;
  }
  .stage {
    position: absolute; inset: 10px;
    background: var(--stage-inner);
  }
  .sheet {
    position: absolute;
    background: var(--paper);
    overflow: hidden;
    box-shadow: 0 2px 6px rgba(0,0,0,.25);
  }
  .brand-circle {
    position: absolute;
    border-radius: 50%;
    background: radial-gradient(circle at 40% 40%, var(--brand-light), var(--brand-blue) 55%, var(--brand-deep));
  }
  .brand-name {
    position: absolute;
    font-family: "Nunito", Arial, sans-serif;
    font-weight: 800;
    color: var(--brand-blue);
    letter-spacing: .04em;
    white-space: nowrap;
  }
  .brand-name--vertical {
    transform: rotate(-90deg);
    transform-origin: left top;
  }

  /* Business card */
  .business-card { left: 24px; top: 329px; width: 156px; height: 139px; }
  .business-card .brand-circle { width: 84px; height: 84px; right: -14px; top: -14px; }
  .business-card .brand-name { left: 10px; bottom: 10px; font-size: 12px; }
  .card-contact {
    position: absolute; left: 10px; top: 54px;
    font-family: "Nunito", Arial, sans-serif;
    font-size: 4.6px; line-height: 1.45; color: var(--ink-soft);
  }
  .card-contact .person { font-size: 6px; font-weight: 700; color: var(--ink); }

  /* Letterhead */
  .letterhead { left: 225px; top: 26px; width: 418px; height: 552px; }
  .letterhead .brand-circle { width: 150px; height: 150px; right: -38px; top: -44px; }
  .letterhead .brand-name--vertical { left: 16px; top: 168px; font-size: 28px; }
  .letter-body {
    position: absolute; left: 66px; top: 76px; width: 296px;
    font-size: 5.6px; line-height: 1.5;
  }
  .letter-body .recipient { font-weight: 700; margin-bottom: 8px; }
  .letter-body p { margin-bottom: 7px; text-align: justify; }
  .signature {
    width: 70px; height: 22px; margin: 6px 0 4px;
    border-radius: 3px;
    background: linear-gradient(90deg, #d9d9d9, #efefef);
  }
  .letter-footer {
    position: absolute; left: 66px; right: 40px; bottom: 16px;
    font-family: "Nunito", Arial, sans-serif;
    font-size: 4.4px; color: var(--ink-soft); text-align: center;
  }

  /* Envelope back */
  .envelope-back { left: 669px; top: 26px; width: 502px; height: 264px; }
  .envelope-flap { position: absolute; left: 0; top: 0; width: 100%; height: 100%; }

  /* Envelope front */
  .envelope-front { left: 669px; top: 326px; width: 502px; height: 252px; }
  .envelope-front .brand-circle { width: 116px; height: 116px; right: -30px; top: -34px; }
  .envelope-front .brand-name--vertical { left: 22px; top: 210px; font-size: 24px; }
  .envelope-return {
    position: absolute; left: 60px; bottom: 14px;
    font-family: "Nunito", Arial, sans-serif;
    font-size: 4.4px; color: var(--ink-soft);
  }
</style>
</head>
<body>
<main class="stage">

  <section class="sheet business-card" aria-label="Business card">
    <div class="brand-circle"></div>
    <div class="card-contact">
      <div class="person">Dean R. Marlow</div>
      <div>President</div>
      <div>418 Bellwick Street Palo Alto, CA 94306</div>
      <div>dean@quevrafin.com</div>
      <div>quevrafin.com</div>
      <div>CA DRE: #00471362, NMLS: #517294</div>
    </div>
    <div class="brand-name">QUEVRAFIN</div>
  </section>

  <section class="sheet letterhead" aria-label="Letterhead">
    <div class="brand-circle"></div>
    <div class="brand-name brand-name--vertical">QUEVRAFIN</div>
    <div class="letter-body">
      <div class="recipient">Lorem Ipsum<br>dolor sit amet<br>consectetuer adipiscing elit.</div>
      <p>Dear reader, thank you for choosing our lending team. We pair modern tools with careful, personal service so every loan moves quickly from first call to closing. Our online portal lets you upload documents, track each step and sign securely from any device, day or night.</p>
      <p>Rates shift daily, so we watch the market for you and alert you the moment a better option appears. Whether you are buying a first home, refinancing or drawing on equity, we explain each choice in plain terms and compare the true cost over the life of the loan.</p>
      <p>Our team has served Palo Alto families for many years, and most of our new clients come through referrals. We are proud of that trust and work hard to earn it again with every file we open.</p>
      <p>Please call or write any time with questions. We look forward to helping you reach your goals.</p>
      <p>Sincerely yours,</p>
      <div class="signature" role="img" aria-label="Handwritten signature"></div>
    </div>
    <div class="letter-footer">418 Bellwick Street Palo Alto, CA 94306 &nbsp;|&nbsp; dean@quevrafin.com &nbsp;|&nbsp; quevrafin.com &nbsp;|&nbsp; CA DRE: #00471362, NMLS: #517294</div>
  </section>

  <section class="sheet envelope-back" aria-label="Envelope back">
    <svg class="envelope-flap" viewBox="0 0 502 264" preserveAspectRatio="none" aria-hidden="true">
      <defs>
        <linearGradient id="flapGradient" x1="0" y1="0" x2="0" y2="1">
          <stop offset="0" stop-color="#0b2c6a"/>
          <stop offset="0.6" stop-color="#1d4fa3"/>
          <stop offset="1" stop-color="#4f86d6"/>
        </linearGradient>
      </defs>
      <path d="M0 0 H502 V60 C430 120 330 168 251 170 C172 168 72 120 0 60 Z" fill="url(#flapGradient)"/>
    </svg>
  </section>

  <section class="sheet envelope-front" aria-label="Envelope front">
    <div class="brand-circle"></div>
    <div class="brand-name brand-name--vertical">QUEVRAFIN</div>
    <div class="envelope-return">418 Bellwick Street Palo Alto, CA 94306 &nbsp;|&nbsp; dean@quevrafin.com &nbsp;|&nbsp; quevrafin.com</div>
  </section>

</main>
</body>
</html>
```